Rollers & Glides.com

Vertical Business Card with focus on branding with our icon. Information on card will be logo, persons name, position, phone number, email address and website. Use the the name Marcus Pellow, position President, phone number 480.915.2267, email Marcus@rollersandglides-demo.com, website www.rollersandglides-demo.com.

```html
<!DOCTYPE html>
<html lang="en">
<head>
<meta charset="UTF-8">
<title>Rollers &amp; Glides.com — Business Card</title>
<link href="https://fonts.googleapis.com/css2?family=Roboto:wght@500&family=Arimo:wght@400;700&display=swap" rel="stylesheet">
<style>
  :root {
    --brand-blue: #3461b1;
    --brand-blue-deep: #2f59a6;
    --paper: #ffffff;
    --paper-shade: #ececec;
    --ink: #1d1d1d;
    --rule: #c9c9c9;
    --stage: #2a2a2a;
  }
  * { box-sizing: border-box; margin: 0; padding: 0; }
  html, body {
    width: 1200px; height: 900px; overflow: hidden;
    background: var(--stage);
  }
  .sheet {
    width: 1200px; height: 900px;
    display: flex; flex-direction: column;
    align-items: center; justify-content: center; gap: 60px;
  }
  .card {
    position: relative;
    width: 560px; height: 320px;
    border-radius: 2px;
    overflow: hidden;
    box-shadow: 0 18px 40px rgba(0,0,0,.55);
  }
  .card-pattern { position: absolute; inset: 0; }
  .card--front .card-pattern {
    background: linear-gradient(135deg, var(--brand-blue) 0%, var(--brand-blue-deep) 100%);
  }
  .card--back .card-pattern {
    background: linear-gradient(160deg, var(--paper) 35%, var(--paper-shade) 100%);
  }
  .brand {
    position: absolute;
    display: flex; flex-direction: column; align-items: center; gap: 18px;
    font-family: 'Roboto', sans-serif; font-weight: 500;
    letter-spacing: 1px;
    white-space: nowrap;
  }
  .brand-dot { border-radius: 50%; }
  .card--front .brand {
    left: 0; right: 0; top: 70px;
    color: var(--paper); font-size: 30px;
  }
  .card--front .brand-dot {
    width: 110px; height: 110px;
    border: 14px solid var(--paper);
  }
  .card--back .brand {
    left: 28px; width: 214px; top: 95px;
    color: var(--brand-blue); font-size: 19px;
  }
  .card--back .brand-dot {
    width: 80px; height: 80px;
    border: 10px solid var(--brand-blue);
  }
  .divider {
    position: absolute; left: 256px; top: 60px;
    width: 1px; height: 200px; background: var(--rule);
  }
  .contact {
    position: absolute; left: 280px; right: 36px; top: 72px;
    font-family: 'Arimo', sans-serif; color: var(--ink);
  }
  .person-name {
    font-weight: 700; font-size: 22px; color: var(--brand-blue);
    text-transform: uppercase; letter-spacing: .2px;
  }
  .person-role { font-size: 16px; margin-bottom: 24px; }
  .contact-list { list-style: none; display: flex; flex-direction: column; gap: 6px; }
  .contact-item {
    display: flex; align-items: center; gap: 9px;
    font-size: 13px; white-space: nowrap;
  }
  .contact-icon { width: 15px; height: 15px; flex: none; fill: var(--brand-blue); }
  .web-domain { color: var(--brand-blue); }
</style>
</head>
<body>
<main class="sheet">

  <section class="card card--front">
    <div class="card-pattern" role="img" aria-label="Faint repeating brand icon pattern on blue"></div>
    <div class="brand">
      <span class="brand-dot"></span>
      <span class="brand-name">Rollers &amp; Glides.com</span>
    </div>
  </section>

  <section class="card card--back">
    <div class="card-pattern" role="img" aria-label="Faint repeating brand icon pattern on white"></div>
    <div class="brand">
      <span class="brand-dot"></span>
      <span class="brand-name">Rollers &amp; Glides.com</span>
    </div>
    <div class="divider"></div>
    <div class="contact">
      <h1 class="person-name">Marcus Pellow</h1>
      <p class="person-role">President</p>
      <ul class="contact-list">
        <li class="contact-item">
          <svg class="contact-icon" viewBox="0 0 24 24" aria-hidden="true"><path d="M6.6 10.8a15.1 15.1 0 0 0 6.6 6.6l2.2-2.2c.3-.3.7-.4 1-.2 1.1.4 2.3.6 3.6.6.6 0 1 .4 1 1V20c0 .6-.4 1-1 1C10.6 21 3 13.4 3 4c0-.6.4-1 1-1h3.5c.6 0 1 .4 1 1 0 1.3.2 2.5.6 3.6.1.3 0 .7-.2 1z"/></svg>
          <span>480.915.2267</span>
        </li>
        <li class="contact-item">
          <svg class="contact-icon" viewBox="0 0 24 24" aria-hidden="true"><path d="M2 5h20v14H2z M3.5 6.5 12 13l8.5-6.5" fill="none" stroke="var(--brand-blue)" stroke-width="2"/><path d="M2 5h20L12 12.5z"/></svg>
          <span>Marcus@rollersandglides-demo.com</span>
        </li>
        <li class="contact-item">
          <svg class="contact-icon" viewBox="0 0 24 24" aria-hidden="true"><g fill="none" stroke="var(--brand-blue)" stroke-width="2"><circle cx="12" cy="12" r="9.5"/><ellipse cx="12" cy="12" rx="4" ry="9.5"/><path d="M2.5 12h19M4 7h16M4 17h16"/></g></svg>
          <span>www.<span class="web-domain">rollersandglides-demo</span>.com</span>
        </li>
      </ul>
    </div>
  </section>

</main>
</body>
</html>
```